Sophisticated, clean website reflecting my feminine, playful side to sell my abstract art,

I need a website no more than 3 pages to showcase my paintings, a little about me and some contact info. I do abstracts so looking for something a little edgy, yet feminine and current.
Updates

Hi there, These are some artists websites that I Iike: Marnelvoss.com (I like how airy it is) peterwallombry.com garethpolvens.com (I like how it scrolls) I'll need a place for a photo ( a headshot-i do not have it yet so I'll need to be able to upload that later) as well as an area for my bio. Also, it's important that I will be able to upload any new photos and descriptions easily so it should be user friendly. Lastly, I like in a sunny place so would like to have this seem upbeat and playful as that is how i like to paint. thanks-I'm trying to upload my photos now -

Target Market(s)

ppl ages 35-70 who want large scale art for their homes

Industry/Entity Type

art

Coding

Coded - Design and coding required

Number of Pages Required

3 page

Colors

Designer to choose colors to be used in the design.

Requirements
Must have
• photos of my art, a place for my bio, be easy to reach me. tasteful-nothing too "in your face" -my clients are pretty high end and organized. They like clean lines
Nice to have
• sophisticated background, muted tones in the back-similar clean font throughout-no cursive
Should not have
• too many dark areas. Too many blocks of color. Too serious.

```html
<!DOCTYPE html>
<html lang="en">
<head>
<meta charset="utf-8">
<title>Mara Ellison — Abstract Paintings</title>
<link rel="stylesheet" href="https://fonts.googleapis.com/css2?family=Heebo:wght@300;400&family=Questrial&family=Nunito+Sans:wght@300;400&display=swap">
<style>
  :root {
    --ink: #111111;
    --text: #333333;
    --muted: #555555;
    --gold: #b9a678;
    --frame: #cdc5b7;
    --rule: #d6d6d6;
    --paper: #ffffff;
    --photo-grey: #eeeeee;
  }
  * { box-sizing: border-box; margin: 0; padding: 0; }
  html, body { width: 1200px; height: 2884px; overflow: hidden; background: var(--paper); }
  body { position: relative; color: var(--text); font-family: "Nunito Sans", sans-serif; }

  .brand { position: absolute; display: flex; align-items: center; gap: 14px; color: var(--ink);
           font-family: "Heebo", sans-serif; font-weight: 300; letter-spacing: 0.5px; white-space: nowrap; }
  .brand-square { background: var(--ink); display: block; }
  .site-header .brand { left: 0; right: 0; top: 24px; justify-content: center; font-size: 45px; line-height: 1; }
  .site-header .brand-square { width: 42px; height: 42px; }
  .header-rule { position: absolute; left: 0; width: 1200px; top: 100px; height: 2px; background: var(--rule); }

  .nav-link { position: absolute; font-family: "Questrial", sans-serif; font-size: 17px; color: #222;
              transform: translateX(-50%); white-space: nowrap; letter-spacing: 0.3px; }
  .main-nav .nav-link { top: 121px; }
  .nav-link.is-active::after { content: ""; position: absolute; left: 2px; right: 2px; bottom: -10px; height: 2px; background: var(--ink); }
  .social { display: flex; align-items: center; gap: 6px; }
  .social-dot { width: 30px; height: 30px; border-radius: 50%; background: var(--ink); display: block; }

  .hero { position: absolute; top: 165px; left: 0; width: 1200px; height: 644px;
          background:
            radial-gradient(ellipse at 75% 20%, rgba(220,200,110,0.75), transparent 35%),
            radial-gradient(ellipse at 20% 60%, rgba(40,130,110,0.8), transparent 45%),
            radial-gradient(ellipse at 90% 80%, rgba(120,80,50,0.6), transparent 35%),
            linear-gradient(135deg, #6fae4a 0%, #2f8a73 40%, #d8dcd4 60%, #4f9a5a 80%, #24677a 100%); }
  .hero-dots { position: absolute; left: 515px; top: 606px; display: flex; gap: 4px; }
  .hero-dots span { width: 40px; height: 4px; background: rgba(255,255,255,0.45); display: block; }
  .hero-dots span.is-current { background: #ffffff; }

  .section-title { position: absolute; font-family: "Heebo", sans-serif; font-weight: 300; color: var(--ink);
                   line-height: 1; white-space: nowrap; }
  .title-rule { position: absolute; height: 2px; width: 63px; background: var(--gold); }

  .portrait-frame { position: absolute; left: 56px; top: 929px; width: 410px; height: 403px;
                    border: 2px solid #cccccc; padding: 8px; }
  .portrait { width: 100%; height: 100%; background: linear-gradient(180deg, #f2f2f2, #e6e6e6); }
  .about .section-title { left: 524px; top: 952px; font-size: 45px; }
  .about .title-rule { left: 524px; top: 1010px; }
  .about-copy { position: absolute; left: 524px; top: 1035px; width: 585px; font-size: 17px; line-height: 27px;
                font-weight: 300; color: var(--muted); }
  .about-copy p + p { margin-top: 14px; }

  .gallery .section-title { left: 0; right: 0; text-align: center; top: 1474px; font-size: 40px; }
  .gallery .title-rule { left: 560px; top: 1527px; }
  .painting-frame { position: absolute; left: 158px; top: 1574px; width: 902px; height: 571px;
                    border: 16px solid var(--frame); background: var(--paper); padding: 0; }
  .painting { width: 100%; height: 100%;
              background:
                radial-gradient(ellipse at 30% 50%, rgba(110,60,150,0.85), transparent 40%),
                radial-gradient(ellipse at 80% 30%, rgba(150,90,170,0.7), transparent 35%),
                radial-gradient(ellipse at 65% 70%, rgba(180,120,90,0.5), transparent 35%),
                linear-gradient(120deg, #3a3550 0%, #8a6a9e 35%, #e6ddd0 60%, #7a5a9a 80%, #2f2e48 100%); }
  .arrow { position: absolute; top: 1830px; width: 26px; height: 42px; }
  .arrow-prev { left: 95px; }
  .arrow-next { left: 1097px; }

  .contact .section-title { left: 0; right: 0; text-align: center; top: 2287px; font-size: 40px; padding-left: 10px; }
  .contact .title-rule { left: 578px; top: 2337px; width: 78px; }
  .contact-lead { position: absolute; left: 0; right: 0; top: 2358px; text-align: center; font-size: 18px; color: #222; }
  .contact-item { position: absolute; display: flex; align-items: center; gap: 12px; font-size: 20px; color: #222;
                  font-family: "Nunito Sans", sans-serif; }
  .contact-icon { width: 42px; height: 42px; border-radius: 50%; background: var(--ink); display: flex;
                  align-items: center; justify-content: center; flex: none; }
  .item-phone { left: 499px; top: 2418px; }
  .item-email { left: 458px; top: 2475px; }
  .item-social { left: 517px; top: 2530px; }

  .site-footer .brand { left: 126px; top: 2731px; font-size: 30px; gap: 10px; }
  .site-footer .brand-square { width: 44px; height: 44px; }
  .site-footer .nav-link { top: 2745px; }
  .footer-rule { position: absolute; left: 120px; width: 992px; top: 2809px; height: 2px; background: var(--rule); }
  .copyright { position: absolute; left: 0; right: 0; top: 2828px; text-align: center; font-family: "Questrial", sans-serif;
               font-size: 14px; color: #333; }
</style>
</head>
<body>

<header class="site-header">
  <div class="brand"><span class="brand-square"></span>MARA ELLISON</div>
  <div class="header-rule"></div>
  <nav class="main-nav">
    <a class="nav-link is-active" style="left:209px">HOME</a>
    <a class="nav-link" style="left:388px">ABOUT ME</a>
    <a class="nav-link" style="left:580px">GALLERY</a>
    <a class="nav-link" style="left:768px">CONTACT</a>
    <a class="nav-link social" style="left:985px; top:116px"><span class="social-dot"></span>@mellisonart</a>
  </nav>
</header>

<section class="hero" role="img" aria-label="Close-up of an abstract painting in greens, teal and ochre brushstrokes">
  <div class="hero-dots"><span class="is-current"></span><span></span><span></span><span></span><span></span></div>
</section>

<section class="about">
  <div class="portrait-frame"><div class="portrait" role="img" aria-label="Artist headshot"></div></div>
  <h2 class="section-title">ABOUT ME</h2>
  <div class="title-rule"></div>
  <div class="about-copy">
    <p>Lorem ipsum dolor sit amet, consectetur adipiscing elit, sed do eiusmod tempor incididunt ut labore et dolore magna aliqua. Ut enim ad minim veniam, quis nostrud exercitation</p>
    <p>Duis aute irure dolor in reprehenderit in voluptate velit esse cillum dolore eu fugiat nulla pariatur. Excepteur sint occaecat cupidatat non proident, sunt in culpa qui officia deserunt mollit anim id est laborum.Sed ut perspiciatis unde pariatur. Excepteur sint occaecat cupidatat non proident, sunt in culpa qui officia deserunt mollit anim id est laborum.Sed ut persmollit anim id est laborum.Sed ut perspiciatis unde pariatur. Excepteur sin</p>
  </div>
</section>

<section class="gallery">
  <h2 class="section-title">PAINTING GALLERY</h2>
  <div class="title-rule"></div>
  <svg class="arrow arrow-prev" viewBox="0 0 26 42" aria-hidden="true"><polyline points="20,4 5,21 20,38" fill="none" stroke="#b9a678" stroke-width="5" stroke-linecap="round" stroke-linejoin="round"/></svg>
  <div class="painting-frame"><div class="painting" role="img" aria-label="Abstract painting in purple, navy and cream with burst-like marks"></div></div>
  <svg class="arrow arrow-next" viewBox="0 0 26 42" aria-hidden="true"><polyline points="6,4 21,21 6,38" fill="none" stroke="#b9a678" stroke-width="5" stroke-linecap="round" stroke-linejoin="round"/></svg>
</section>

<section class="contact">
  <h2 class="section-title">CONTACT ME</h2>
  <div class="title-rule"></div>
  <p class="contact-lead">Please get in touch with me on below details.</p>
  <div class="contact-item item-phone">
    <span class="contact-icon"><svg width="22" height="22" viewBox="0 0 24 24"><path fill="#fff" d="M6.6 10.8a15.1 15.1 0 0 0 6.6 6.6l2.2-2.2c.3-.3.7-.4 1-.2 1.1.4 2.3.6 3.6.6.6 0 1 .4 1 1V20c0 .6-.4 1-1 1A17 17 0 0 1 3 4c0-.6.4-1 1-1h3.5c.6 0 1 .4 1 1 0 1.3.2 2.5.6 3.6.1.3 0 .7-.2 1z"/></svg></span>
    (555) 014 2290
  </div>
  <div class="contact-item item-email">
    <span class="contact-icon"><svg width="24" height="18" viewBox="0 0 24 18"><rect x="1.5" y="1.5" width="21" height="15" rx="1.5" fill="none" stroke="#fff" stroke-width="2"/><polyline points="2,2 12,10 22,2" fill="none" stroke="#fff" stroke-width="2"/></svg></span>
    maraellison@studio.com
  </div>
  <div class="contact-item item-social">
    <span class="contact-icon"></span>
    @mellisonart
  </div>
</section>

<footer class="site-footer">
  <div class="brand"><span class="brand-square"></span>MARA ELLISON</div>
  <a class="nav-link" style="left:541px">ABOUT ME</a>
  <a class="nav-link" style="left:686px">GALLERY</a>
  <a class="nav-link" style="left:829px">CONTACT</a>
  <a class="nav-link social" style="left:1013px; top:2738px"><span class="social-dot"></span>@mellisonart</a>
  <div class="footer-rule"></div>
  <p class="copyright">© 2022 Mara Ellison &nbsp; All Rights Reserved</p>
</footer>

</body>
</html>
```